Creative, fresh business card design for Ripplecraft Facades

We need a fresh, creative business card design for Ripplecraft Facades. We are the manufacturer of Ripplecraft Facades in Australia. Wall panels are 2400 x 1200mm panels made from MDF and feature 3D patterns on the face of the panel. The colours to be used are green, silver/grey and white RGB
Red 187
Green 207
Blue 65.

An idea is to possibly use a watermark of one of our designs as a background (like on the "Grids" design on the left hand side of page 2 of our brochure).

Target Market(s)

Interior designers, architects, builders and home renovators

Industry/Entity Type

Business

Contact Information for Business Card

Details to go on the card are:
Our logo (attached),
Slogan: "Decorative panels for interiors and exteriors",
Contact name,
Position,
Mobile phone number,
Business address,
Business phone,
Business fax,
Website and
Email address.

I have attached a few images of our panels and our brochure for reference.

The colours of the business card should feature our logo colours which are: RGB
Red 187
Green 207
Blue 65

Requirements
Must have
• Very modern fonts and design. Some of the designs shown especially the "Prisms" design which is a popular design.
Nice to have
• Creative but simple design. Very contemporary.
Should not have
• Anything ornate or old fashioned.

```html
<!DOCTYPE html>
<html lang="en">
<head>
<meta charset="utf-8">
<title>Ripplecraft Facades – Business Card</title>
<link rel="stylesheet" href="https://fonts.googleapis.com/css2?family=Questrial&display=swap">
<style>
  :root {
    --page-bg: #e6e3dd;
    --card-black: #111111;
    --card-shade: #1c1c1c;
    --lime: #bbcf41;
    --silver: #c9c9c9;
    --text-grey: #b5b5b5;
  }
  * { margin: 0; padding: 0; box-sizing: border-box; }
  html, body { width: 1200px; height: 1022px; overflow: hidden; }
  body {
    background: var(--page-bg);
    font-family: "Questrial", "Helvetica Neue", Arial, sans-serif;
    position: relative;
  }
  .business-card {
    position: absolute;
    left: 150px;
    top: 254px;
    width: 900px;
    height: 514px;
    background: var(--card-black);
    border-radius: 4px;
    overflow: hidden;
    box-shadow: 0 18px 40px rgba(0,0,0,0.35);
  }
  .ripple-texture {
    position: absolute;
    inset: 0;
    background:
      radial-gradient(circle at 30% 60%, var(--card-shade) 0%, transparent 45%),
      radial-gradient(circle at 75% 35%, var(--card-shade) 0%, transparent 40%),
      var(--card-black);
  }
  .brand {
    position: absolute;
    right: 56px;
    top: 48px;
    display: flex;
    align-items: center;
    gap: 16px;
  }
  .brand-square {
    width: 58px;
    height: 58px;
    background: var(--lime);
  }
  .brand-name {
    font-size: 34px;
    color: var(--silver);
    letter-spacing: 0.5px;
  }
  .slogan {
    position: absolute;
    right: 56px;
    top: 120px;
    width: 330px;
    font-size: 15px;
    line-height: 1.35;
    letter-spacing: 2.4px;
    color: var(--text-grey);
  }
  .contact-list {
    position: absolute;
    left: 534px;
    top: 192px;
    list-style: none;
  }
  .contact-list li {
    display: flex;
    align-items: center;
    gap: 14px;
    height: 32px;
    font-size: 19px;
    letter-spacing: 1.6px;
    color: var(--text-grey);
  }
  .contact-list svg { width: 18px; height: 18px; flex: none; }
  .address {
    position: absolute;
    left: 566px;
    top: 384px;
    font-size: 19px;
    line-height: 1.45;
    letter-spacing: 1.6px;
    color: var(--text-grey);
  }
  .person {
    position: absolute;
    left: 70px;
    top: 352px;
  }
  .person-name {
    font-size: 36px;
    color: var(--lime);
    letter-spacing: 0.5px;
  }
  .person-title {
    margin-top: 2px;
    font-size: 18px;
    color: var(--text-grey);
    letter-spacing: 1px;
  }
</style>
</head>
<body>
  <section class="business-card">
    <div class="ripple-texture" role="img" aria-label="Faint embossed ripple pattern across the black card"></div>

    <div class="brand">
      <div class="brand-square"></div>
      <div class="brand-name">Ripplecraft Facades</div>
    </div>
    <p class="slogan">decorative panels for interiors &amp; landscapes</p>

    <ul class="contact-list">
      <li>
        <svg viewBox="0 0 18 18"><rect x="5" y="1" width="8" height="16" rx="1.5" fill="var(--lime)"/><rect x="6.5" y="3" width="5" height="9" fill="#111"/></svg>
        612. 480. 3917
      </li>
      <li>
        <svg viewBox="0 0 18 18"><path d="M4 2 L7 2 L8 6 L6 7.5 C7 10 8 11 10.5 12 L12 10 L16 11 L16 14 C16 15 15 16 14 16 C8 16 2 10 2 4 C2 3 3 2 4 2 Z" fill="var(--lime)"/></svg>
        612. 480. 3920
      </li>
      <li>
        <svg viewBox="0 0 18 18"><rect x="5" y="1.5" width="8" height="5" fill="var(--lime)"/><rect x="2" y="7" width="14" height="6" rx="1" fill="var(--lime)"/><rect x="5" y="11" width="8" height="5.5" fill="var(--lime)" stroke="#111" stroke-width="1"/></svg>
        612. 480. 3921
      </li>
      <li>
        <svg viewBox="0 0 18 18"><rect x="1.5" y="3.5" width="15" height="11" fill="var(--lime)"/><path d="M1.5 3.5 L9 10 L16.5 3.5 M1.5 14.5 L7 8.5 M16.5 14.5 L11 8.5" fill="none" stroke="#111" stroke-width="1.2"/></svg>
        daniel@ripplecraft.com
      </li>
      <li>
        <svg viewBox="0 0 18 18"><circle cx="9" cy="9" r="7.5" fill="var(--lime)"/><path d="M1.5 9 H16.5 M9 1.5 V16.5 M9 1.5 C5 5 5 13 9 16.5 M9 1.5 C13 5 13 13 9 16.5" fill="none" stroke="#111" stroke-width="1.1"/></svg>
        www.ripplecraft.com
      </li>
    </ul>

    <p class="address">412 Harbour Lane<br>Kelvin Bay, NSW 2031</p>

    <div class="person">
      <p class="person-name">Daniel Horvath</p>
      <p class="person-title">President</p>
    </div>
  </section>
</body>
</html>
```